Doctor Formulated Medical Cosmetics

Velour Skinhaus is an E-commerce site for high end Medical Cosmetics designed to treat specific skin problems. The Velour Skinhaus difference/advantage is that all creams and serums are:
Doctor Formulated, Freshly Handmade, Registered Pharmacy.
The Site also provides real doctor Dermatology Consultations, Library (with a list of - 1. Active Ingredients in the creams with description of their effects, 2. Skin Conditions with information on what causes the condition and typical treatment approaches and outcomes. 3. Resources from Dermatology Journals and literature on the conditions.)
Header Information: Velour Skinhaus, languages EN, BG, Register / log in, Shopping Bag. This field should be narrow.
Categories (horizontal): Home, Face, Body, Hair Care, Skin Conditions, Doctor Consultation, Library
The Landing Page should have only one well organized picture, which is intended to create the feeling of luxury, freedom and relaxation. It will be large and will fill the whole screen. All text should be on transparent or similar color fields. Please use the color of the text to create also the feeling of conservative luxury.
Written message / image overlay Velour Skinhaus(logo), Skin Care, Doctor Formulated, Freshly Handmade, Registered Pharmacy.
Please study the Landing Page of this site as an example: www.marivane.com
Under the Landing Page, there should be a slider with 4 of our products.
Underneath: Four Blog Articles (large pictures for maximum impact and luxury text underneath).
Underneath: Banner for Dermatologist Consultation, (button for Start Your Case Now).
Underneath: Two pictures in a line - Library (with books), and Active Ingredients.
Footer: Philosophy, Categories, Customer Care
Please adhere to the color palate provided in the pictures (as attachments). Provided are some examples of Web Sites with the desired look and feel. www.quillora.com , www.tavenholtmd.com .
Please use different shades of gray, white, beige and gold colors, and black. Our products will be in brown glass jars and bottles to convey the professional, pharmacy made nature of the creams and lotions.
We find the following Front Page very attractive and effective - www.marivane.com , with its full page image and overlaying text.
Please have a look at this link for the Landing page.
http://www.brimlensphoto.com/detail/video/woman-lying-on-a-black-sand-beach-in-a-bikini-stock-footage/58213067
I would like to use it in the animated version to achieve the WOW effect. I have uploaded the jpeg version for it, so you will be able create your design.
For the Landing page design, please use only the two uploaded pictures of a woman laying at the beach. Let's see how each of them will look like.
Thank you for your help.

```html
<!DOCTYPE html>
<html lang="en">
<head>
<meta charset="utf-8">
<title>Velour Skinhaus — Doctor Formulated Medical Cosmetics</title>
<link rel="stylesheet" href="https://fonts.googleapis.com/css2?family=Marcellus&family=Lato:wght@400;700;900&family=PT+Sans:wght@400;700&display=swap">
<style>
:root{
  --black:#050505;
  --gold:#d3b06a;
  --gold-light:#e2c58a;
  --gold-dark:#b8924a;
  --brown:#6d4b24;
  --brown-nav:#7a5529;
  --brown-deep:#573a1a;
  --ink:#2a2a2a;
  --grey:#6b6b6b;
  --page:#e9e5de;
  --white:#ffffff;
  --line:#e3ddd2;
}
*{box-sizing:border-box;margin:0;padding:0}
html,body{width:1200px;height:2857px;overflow:hidden}
body{position:relative;background:var(--page);font-family:"Lato",Arial,sans-serif;color:var(--ink)}
.abs{position:absolute}
a{color:inherit;text-decoration:none}
ul{list-style:none}

/* header */
.site-header{left:0;top:0;width:1200px;height:131px;background:var(--black)}
.brand{display:flex;align-items:center;gap:12px;font-family:"Marcellus",serif;color:var(--gold);font-size:38px;white-space:nowrap}
.brand-dot{width:34px;height:34px;border:2px solid var(--gold);border-radius:50%}
.site-header .brand{position:absolute;left:99px;top:40px}
.top-links{position:absolute;left:606px;top:14px;display:flex;align-items:center;font-size:13px;color:var(--white)}
.top-links li{display:flex;align-items:center;gap:8px;padding:0 14px;border-left:1px solid #444}
.top-links li:first-child{padding-left:0;border-left:0}
.top-icon{width:26px;height:26px;border-radius:50%;background:var(--gold);display:flex;align-items:center;justify-content:center}
.lang-flag{width:26px;height:26px;border-radius:50%;background:#b8c4d8}
.search-box{position:absolute;left:606px;top:69px;width:236px;height:38px;background:var(--white);border-radius:2px;display:flex;align-items:center;justify-content:space-between;padding:0 10px;font-size:12px;font-style:italic;color:#555}
.cart-box{position:absolute;left:870px;top:69px;width:231px;height:38px;background:var(--white);border-radius:2px;display:flex;align-items:center;gap:12px;padding:0 12px;font-size:12px;font-style:italic;color:#555}

/* nav */
.main-nav{left:0;top:131px;width:1200px;height:42px;background:var(--brown-nav)}
.main-nav ul{position:absolute;left:99px;top:0;display:flex;height:42px}
.main-nav li{display:flex;align-items:center;padding:0 22px;font-size:15px;color:var(--white);border-right:1px solid #8f6a3c}
.main-nav li:last-child{border-right:0}
.main-nav li.is-active{background:var(--gold);color:var(--brown-deep);padding:0 23px}

/* hero */
.hero{left:0;top:173px;width:1200px;height:579px;overflow:hidden;background:linear-gradient(90deg,#1d1e20 0%,#2d2f32 40%,#4a3d36 62%,#8c6b58 75%,#3a2a22 100%)}
.hero-model{position:absolute;left:630px;top:0;width:570px;height:579px;background:radial-gradient(ellipse at 45% 45%,#c9987c 0%,#8e5f45 35%,#4a2f22 70%,rgba(40,28,22,0) 100%)}
.hero-products{position:absolute;left:105px;top:245px;width:505px;height:290px;border-radius:8px;background:radial-gradient(ellipse at 50% 55%,#f4f4f4 0%,#cfd0d2 55%,rgba(60,60,62,0) 100%)}
.hero-copy{position:absolute;left:101px;top:70px;color:var(--white)}
.hero-kicker{font-family:"Marcellus",serif;font-size:33px}
.hero-title{font-family:"Marcellus",serif;font-size:54px;color:var(--gold-light);line-height:1.05;margin-top:4px;letter-spacing:1px}
.hero-sub{font-family:"Marcellus",serif;font-size:35px;letter-spacing:1px}
.hero-badge{position:absolute;left:392px;top:150px;width:164px;height:164px}
.hero-arrow{position:absolute;top:283px}

/* values */
.values{left:0;top:752px;width:1200px;height:357px;background:var(--gold)}
.value{position:absolute;top:26px;width:230px;text-align:center;color:var(--white)}
.value-ring{width:222px;height:222px;margin:0 auto;border-radius:50%;border:3px dashed rgba(255,255,255,.75);padding:8px}
.value-photo{width:100%;height:100%;border-radius:50%}
.value-name{margin-top:26px;font-family:"PT Sans",sans-serif;font-weight:700;font-size:23px;line-height:1.2}

/* content panel */
.content-panel{left:99px;top:1109px;width:1002px;height:977px;background:var(--white)}
.section-title{position:absolute;width:100%;text-align:center;font-family:"PT Sans",sans-serif;font-weight:700;font-size:35px;color:#222}
.divider{position:absolute;display:flex;align-items:center;gap:10px}
.divider span{height:1px;background:var(--gold)}
.divider i{width:36px;height:36px;border:2px solid var(--gold);border-radius:50%;display:block}
.product{position:absolute;top:1273px;width:221px;height:274px;border:1px solid var(--line);text-align:center}
.product-photo{width:150px;height:148px;margin:12px auto 0}
.stars{margin-top:12px;color:var(--gold);font-size:12px;letter-spacing:1px}
.product-name{margin-top:6px;font-size:13px;color:#222}
.product-price{margin-top:8px;font-size:15px;color:#222}
.product-price s{font-size:12px;color:#888;margin-left:4px}
.btn-buy{position:absolute;left:66px;bottom:-19px;width:88px;height:30px;background:var(--gold);color:var(--white);font-size:12px;display:flex;align-items:center;justify-content:center}
.pager{position:absolute;display:flex;gap:6px}
.pager b{width:22px;height:22px;background:var(--gold);display:flex;align-items:center;justify-content:center}

/* blog */
.blog-band{left:80px;top:1686px;width:1040px;height:348px;background:var(--brown)}
.blog-card{left:126px;top:1709px;width:611px;height:301px;background:var(--white)}
.blog-heading{position:absolute;left:24px;top:20px;font-family:"PT Sans",sans-serif;font-weight:700;font-size:26px;color:#222}
.blog-post{position:absolute;top:72px;width:265px}
.blog-photo{height:104px;margin-left:40px;border-radius:4px}
.blog-date{position:absolute;left:0;top:10px;width:38px;height:56px;background:var(--gold);color:var(--white);text-align:center;font-size:11px;font-weight:700;line-height:1.1;padding-top:6px;clip-path:polygon(0 0,100% 0,100% 100%,50% 84%,0 100%)}
.blog-date b{display:block;font-size:17px}
.blog-title{margin-top:18px;font-size:14px;font-weight:700;color:#111}
.blog-text{margin-top:6px;font-size:12px;line-height:1.35;color:#333}
.read-more{margin-top:8px;display:block;font-size:13px;color:#222}
.arrow-pair{position:absolute;right:24px;top:24px;display:flex;gap:8px}
.arrow-pair b{width:22px;height:22px;background:var(--gold);display:flex;align-items:center;justify-content:center}
.feature-card{left:762px;top:1709px;width:312px;height:297px;border:5px solid #e7e2da;background:linear-gradient(135deg,#9a9a9d,#6f7073 60%,#8d8d90);color:var(--white);text-align:center}
.feature-card h3{margin-top:100px;font-family:"PT Sans",sans-serif;font-size:22px;font-weight:700}
.feature-card h4{margin-top:8px;font-size:14px;font-weight:700}
.feature-card p{margin:6px 28px 0;font-size:12px;line-height:1.35}
.btn-more{display:inline-flex;align-items:center;gap:10px;margin-top:16px;height:28px;padding:0 4px 0 16px;background:var(--gold);border-radius:14px;font-size:11px;font-weight:700}
.btn-more i{width:22px;height:22px;border-radius:50%;background:var(--white);display:flex;align-items:center;justify-content:center}

/* services */
.services{left:0;top:2090px;width:1200px;height:297px;background:linear-gradient(90deg,#2f4a2c 0%,#4f6b45 30%,#6b7d5a 45%,#3e5a35 70%,#24391f 100%)}
.service{position:absolute;top:70px;width:330px;text-align:center;color:var(--white)}
.service h3{margin-top:18px;font-family:"PT Sans",sans-serif;font-weight:700;font-size:28px}
.service p{margin-top:4px;font-size:18px;font-weight:700}

/* newsletter */
.newsletter{left:0;top:2387px;width:1200px;height:103px;background:var(--gold)}
.nl-icon{position:absolute;left:101px;top:30px;width:44px;height:44px;border:2px solid var(--brown);border-radius:50%;display:flex;align-items:center;justify-content:center}
.nl-title{position:absolute;left:154px;top:34px;font-family:"PT Sans",sans-serif;font-weight:700;font-size:26px;color:var(--brown-deep)}
.nl-hint{position:absolute;left:387px;top:44px;font-size:13px;color:var(--brown-deep)}
.nl-input{position:absolute;left:587px;top:38px;width:388px;height:42px;background:var(--white);font-size:12px;color:#444;display:flex;align-items:center;padding-left:36px}
.nl-button{position:absolute;left:975px;top:38px;width:126px;height:42px;background:var(--brown);color:var(--white);font-weight:700;font-size:16px;display:flex;align-items:center;justify-content:center}

/* footer */
.site-footer{left:0;top:2490px;width:1200px;height:310px;background:var(--brown)}
.footer-col{position:absolute;top:30px;width:230px;height:258px;background:rgba(0,0,0,.06);box-shadow:6px 0 10px rgba(0,0,0,.12);padding-left:2px}
.footer-col h4{font-size:14px;font-weight:700;color:var(--white);letter-spacing:.5px;padding-bottom:10px;border-bottom:1px solid rgba(255,255,255,.35);width:177px}
.footer-col ul{margin-top:12px;padding-left:18px}
.footer-col li{position:relative;font-size:12px;color:var(--white);line-height:23px}
.footer-col li::before{content:"";position:absolute;left:-14px;top:10px;width:4px;height:4px;border-radius:50%;background:var(--white)}
.footer-col li.is-active{font-weight:700}
.footer-brand{left:863px;top:2590px;width:238px;justify-content:center;font-size:30px}
.social{left:911px;top:2662px;display:flex;gap:6px}
.social i{width:26px;height:26px;border:1px solid var(--gold);border-radius:50%;display:block}
.bottom-bar{left:0;top:2800px;width:1200px;height:57px;background:var(--brown-deep);color:var(--white);font-size:12px}
.copyright{position:absolute;left:101px;top:21px;font-weight:700}
.accept{position:absolute;left:830px;top:16px;display:flex;align-items:center;gap:6px;font-weight:700}
.accept span{margin-right:6px}
.card-slot{width:36px;height:23px;background:#f3efe6;border-radius:2px}
</style>
</head>
<body>

<header class="site-header abs">
  <div class="brand"><span>Velour Skinhaus</span></div>
  <ul class="top-links">
    <li><span class="top-icon"><svg width="14" height="14" viewBox="0 0 14 14"><circle cx="7" cy="5" r="3" fill="#fff"/><path d="M1 14c0-4 3-5 6-5s6 1 6 5z" fill="#fff"/></svg></span>My Account</li>
    <li><span class="top-icon"><svg width="14" height="14" viewBox="0 0 14 14"><path d="M5 1h4v4h4v4H9v4H5V9H1V5h4z" fill="#fff"/></svg></span>Pharmacy</li>
    <li><span class="top-icon"><svg width="14" height="14" viewBox="0 0 14 14"><rect x="2" y="6" width="10" height="7" fill="#fff"/><path d="M4 6V4a3 3 0 0 1 6 0v2" stroke="#fff" stroke-width="1.6" fill="none"/></svg></span>Register / log in</li>
    <li><span class="lang-flag"></span>English <svg width="10" height="6" viewBox="0 0 10 6"><path d="M0 0h10L5 6z" fill="#999"/></svg></li>
  </ul>
  <div class="search-box"><span>Search</span><svg width="16" height="16" viewBox="0 0 16 16"><circle cx="6.5" cy="6.5" r="4.5" stroke="#d3b06a" stroke-width="2" fill="none"/><path d="M10 10l4 4" stroke="#d3b06a" stroke-width="2"/></svg></div>
  <div class="cart-box"><svg width="22" height="18" viewBox="0 0 22 18"><path d="M1 2h4l3 10h10l3-7H7" stroke="#d3b06a" stroke-width="2" fill="none"/><circle cx="9" cy="16" r="1.6" fill="#d3b06a"/><circle cx="17" cy="16" r="1.6" fill="#d3b06a"/></svg><span>Your cart is empty</span></div>
</header>

<nav class="main-nav abs">
  <ul>
    <li class="is-active">Home</li><li>Face</li><li>Body</li><li>Hair Care</li><li>Skin Concerns</li><li>Dermatologist Consultation</li><li>Library</li><li>Contact Us</li>
  </ul>
</nav>

<section class="hero abs">
  <div class="hero-model" role="img" aria-label="Portrait of a woman with long flowing brown hair"></div>
  <div class="hero-products" role="img" aria-label="White jars, bottle and pen of the skin care range with a swirl of cream"></div>
  <div class="hero-copy">
    <p class="hero-kicker">New Arrivals</p>
    <h1 class="hero-title">BUY 2 ITEMS</h1>
    <p class="hero-sub">GET ONE FOR FREE</p>
  </div>
  <svg class="hero-badge" viewBox="0 0 164 164">
    <polygon points="82,0 101,36 140,24 128,63 164,82 128,101 140,140 101,128 82,164 63,128 24,140 36,101 0,82 36,63 24,24 63,36" fill="#e2c27a"/>
    <text x="82" y="74" text-anchor="middle" font-family="Marcellus, serif" font-size="30" fill="#fff">only</text>
    <text x="82" y="112" text-anchor="middle" font-family="Marcellus, serif" font-size="40" fill="#fff">$25</text>
  </svg>
  <svg class="hero-arrow" style="left:62px" width="22" height="40" viewBox="0 0 22 40"><path d="M20 2L3 20l17 18" stroke="#fff" stroke-width="2" fill="none"/></svg>
  <svg class="hero-arrow" style="left:1118px" width="22" height="40" viewBox="0 0 22 40"><path d="M2 2l17 18L2 38" stroke="#fff" stroke-width="2" fill="none"/></svg>
</section>

<section class="values abs">
  <div class="value" style="left:95px"><div class="value-ring"><div class="value-photo" role="img" aria-label="Smiling doctor in a white coat beside cosmetic products" style="background:radial-gradient(circle at 60% 40%,#f4f1ee,#d9d3cf 60%,#b9aea8)"></div></div><p class="value-name">Doctor<br>Formulated</p></div>
  <div class="value" style="left:352px"><div class="value-ring"><div class="value-photo" role="img" aria-label="Handmade cream in bowls on a wooden board" style="background:radial-gradient(circle at 50% 45%,#f2e3c2,#c89a5e 55%,#8a5d2f)"></div></div><p class="value-name">Freshly<br>Handmade</p></div>
  <div class="value" style="left:611px"><div class="value-ring"><div class="value-photo" role="img" aria-label="Registered pharmacy seal" style="background:radial-gradient(circle,#fff 0 58%,#e6cd8e 60% 100%)"></div></div><p class="value-name">Registered<br>Pharmacy</p></div>
  <div class="value" style="left:872px"><div class="value-ring"><div class="value-photo" role="img" aria-label="Coloured puzzle pieces fitting together" style="background:radial-gradient(circle at 45% 45%,#c9c9c9,#8c8c8c 60%,#5e5e5e)"></div></div><p class="value-name">Highest Ethical<br>Standards</p></div>
</section>

<main class="content-panel abs">
  <h2 class="section-title" style="top:34px">Featured Products</h2>
  <div class="divider" style="left:334px;top:112px"><span style="width:150px"></span><i></i><span style="width:150px"></span></div>
  <div class="pager" style="left:476px;top:500px">
    <b><svg width="8" height="10" viewBox="0 0 8 10"><path d="M6 1L2 5l4 4" stroke="#fff" stroke-width="2" fill="none"/></svg></b>
    <b><svg width="8" height="10" viewBox="0 0 8 10"><path d="M2 1l4 4-4 4" stroke="#fff" stroke-width="2" fill="none"/></svg></b>
  </div>
</main>

<article class="product" style="left:122px"><div class="product-photo" role="img" aria-label="Silver serum pump bottle" style="background:linear-gradient(90deg,#fff 25%,#b9bcbf 40%,#e8e9ea 50%,#8f9396 60%,#fff 75%)"></div><p class="stars">★★★☆☆</p><p class="product-name">Lorem ipsum dolor sit amet</p><p class="product-price">$300.00 <s>$380.00</s></p><a class="btn-buy">BUY NOW</a></article>
<article class="product" style="left:366px"><div class="product-photo" role="img" aria-label="Blue cleanser pump bottle" style="background:linear-gradient(90deg,#fff 28%,#8fb5dd 40%,#cfe2f3 50%,#6c9acb 62%,#fff 74%)"></div><p class="stars">★★★☆☆</p><p class="product-name">Lorem ipsum dolor sit amet</p><p class="product-price">$300.00 <s>$380.00</s></p><a class="btn-buy">BUY NOW</a></article>
<article class="product" style="left:610px"><div class="product-photo" role="img" aria-label="Amber glass dropper bottle" style="background:linear-gradient(90deg,#fff 32%,#8a4a1c 42%,#c47a3d 50%,#6a3612 60%,#fff 70%)"></div><p class="stars">★★★☆☆</p><p class="product-name">Lorem ipsum dolor sit amet</p><p class="product-price">$300.00 <s>$380.00</s></p><a class="btn-buy">BUY NOW</a></article>
<article class="product" style="left:855px"><div class="product-photo" role="img" aria-label="Taupe lotion bottle" style="background:linear-gradient(90deg,#fff 30%,#8e8a78 40%,#b6b2a0 50%,#76725f 62%,#fff 72%)"></div><p class="stars">★★★☆☆</p><p class="product-name">Lorem ipsum dolor sit amet</p><p class="product-price">$300.00 <s>$380.00</s></p><a class="btn-buy">BUY NOW</a></article>

<section class="blog-band abs"></section>
<section class="blog-card abs">
  <h2 class="blog-heading">Latest Blog Posts</h2>
  <div class="divider" style="left:244px;top:22px"><i style="width:30px;height:30px"></i><span style="width:140px"></span></div>
  <div class="arrow-pair">
    <b><svg width="8" height="10" viewBox="0 0 8 10"><path d="M6 1L2 5l4 4" stroke="#fff" stroke-width="2" fill="none"/></svg></b>
    <b><svg width="8" height="10" viewBox="0 0 8 10"><path d="M2 1l4 4-4 4" stroke="#fff" stroke-width="2" fill="none"/></svg></b>
  </div>
  <div class="blog-post" style="left:26px">
    <div class="blog-photo" role="img" aria-label="Bowl of golden oil with amber bottles and lemon" style="background:radial-gradient(ellipse at 50% 55%,#e3b33e,#c8892a 45%,#fff 80%)"></div>
    <div class="blog-date"><b>01</b>SEP</div>
    <h3 class="blog-title">Sed ut perspiciatis unde iste mo</h3>
    <p class="blog-text">Duis autem vel eum iriure dolor in hendrerit ink vulput ate velit esse molestie facilisis.</p>
    <a class="read-more">Read More ››</a>
  </div>
  <div class="blog-post" style="left:337px">
    <div class="blog-photo" role="img" aria-label="White and green skin care bottles with leaves" style="background:radial-gradient(ellipse at 50% 55%,#d7ddd0,#6f9a4a 50%,#fff 82%)"></div>
    <div class="blog-date"><b>01</b>SEP</div>
    <h3 class="blog-title">Sed ut perspiciatis unde iste mo</h3>
    <p class="blog-text">Duis autem vel eum iriure dolor in hendrerit ink vulput ate velit esse molestie facilisis.</p>
    <a class="read-more">Read More ››</a>
  </div>
</section>
<aside class="feature-card abs" role="img" aria-label="Woman touching her cheek, muted grey tone">
  <h3>Doctor Formulated</h3>
  <h4>Sed ut perspiciatis unde iste mo</h4>
  <p>Duis autem vel eum iriure dolor in hendrerit ink vulput ate velit esse molestie facilisis.</p>
  <a class="btn-more">READ MORE <i><svg width="8" height="10" viewBox="0 0 8 10"><path d="M2 1l4 4-4 4" stroke="#d3b06a" stroke-width="2" fill="none"/></svg></i></a>
</aside>

<section class="services abs" role="img" aria-label="Woman with closed eyes against soft green foliage">
  <div class="service" style="left:58px">
    <svg width="80" height="64" viewBox="0 0 80 64"><rect x="4" y="14" width="42" height="30" fill="#d3b06a"/><path d="M46 22h16l12 12v10H46z" fill="#d3b06a"/><circle cx="18" cy="48" r="7" fill="#d3b06a" stroke="#3e5a35" stroke-width="3"/><circle cx="60" cy="48" r="7" fill="#d3b06a" stroke="#3e5a35" stroke-width="3"/></svg>
    <h3>FREE SHIPPING</h3><p>ON ORDERS OVER $450.00</p>
  </div>
  <div class="service" style="left:445px">
    <svg width="70" height="64" viewBox="0 0 70 64"><path d="M35 6a26 26 0 1 1-22 12" stroke="#d3b06a" stroke-width="6" fill="none"/><path d="M4 12l14 2-4 13z" fill="#d3b06a"/><path d="M28 44c0-14 8-20 18-22-2 12-8 20-18 22z" fill="#d3b06a"/></svg>
    <h3>ECO-FRIENDLY</h3><p>Help The Environment</p>
  </div>
  <div class="service" style="left:795px">
    <svg width="70" height="64" viewBox="0 0 70 64"><path d="M14 6l10 12-6 6c4 8 10 14 18 18l6-6 12 10-6 10C26 56 8 38 4 16z" fill="#d3b06a"/><text x="50" y="26" text-anchor="middle" font-family="Lato, sans-serif" font-weight="900" font-size="16" fill="#d3b06a">24</text><path d="M36 10a18 18 0 0 1 28 12" stroke="#d3b06a" stroke-width="3" fill="none"/></svg>
    <h3>CUSTOMER SUPPORT</h3><p>WE ARE HERE FOR YOU!</p>
  </div>
</section>

<section class="newsletter abs">
  <div class="nl-icon"><svg width="22" height="18" viewBox="0 0 22 18"><rect x="1" y="3" width="20" height="14" stroke="#6d4b24" stroke-width="2" fill="none"/><path d="M1 3l10 8 10-8" stroke="#6d4b24" stroke-width="2" fill="none"/></svg></div>
  <h2 class="nl-title">NewsLetter Signup</h2>
  <p class="nl-hint">Enter your email address Here</p>
  <div class="nl-input">Enter Email Address</div>
  <a class="nl-button">SUBSCRIBE</a>
</section>

<footer class="site-footer abs">
  <div class="footer-col" style="left:99px"><h4>QUICK LINKS</h4><ul><li class="is-active">Home</li><li>Face</li><li>Body</li><li>Hair Care</li><li>Skin Concerns</li><li>Dermatologist Consultation</li><li>Library</li><li>Contact Us</li></ul></div>
  <div class="footer-col" style="left:381px"><h4>INFORMATION</h4><ul><li>Specials</li><li>New products</li><li>Top sellers</li><li>Our stores</li><li>Delivery</li><li>About us</li><li>Support</li><li>Blog</li></ul></div>
  <div class="footer-col" style="left:621px"><h4>CUSTOMER SERVICE</h4><ul><li>Shipping Policy</li><li>Refunds &amp; Returns</li><li>Contact Support</li></ul></div>
</footer>
<div class="brand footer-brand abs"><span>Velour Skinhaus</span></div>
<div class="social abs"><i></i><i></i><i></i><i></i><i></i></div>
<div class="bottom-bar abs">
  <p class="copyright">Copyright © 2016 Velour Skinhaus. All Rights Reserved.</p>
  <div class="accept"><span>We Accept:</span><i class="card-slot"></i><i class="card-slot"></i><i class="card-slot"></i><i class="card-slot"></i><i class="card-slot"></i></div>
</div>

</body>
</html>
```